Commercial Loan Originator Business Card (CHANGE COLORS SCHEME)

CHANGE COLOR SCHEME - SAME DESIGN

Name Marlene Agate
Title Commercial Loan Originator
Office (800) 417-2906 x68
Direct (240) 615-2043
Email freshgreens4life@quillbox.example

Name Dale Morrow
Office (800) 417-2906 x70
Direct (410) 392-5184
Email d.morthehomeguy@quillbox.example

Name Leonard Vasko
Office (800) 417-2906 x71
Direct (215) 463-0712
Email l.vasko41@quillbox.example

Name Gwen Halsey
Office (800) 417-2906 x
Direct (202) 548-1370
Email ghalsey63@quillbox.example

Name Mirna Ashby
Office (800) 417-2906 x72
Direct (240) 871-4526
Email tristatehomelending@quillbox.example

```html
<!DOCTYPE html>
<html lang="en">
<head>
<meta charset="utf-8">
<title>Leonard Vasko – Business Card</title>
<link href="https://fonts.googleapis.com/css2?family=Playfair+Display:wght@800&family=Raleway:wght@300&family=Poppins:wght@400&display=swap" rel="stylesheet">
<style>
  :root {
    --page-bg: #cbcbcb;
    --card-white: #ffffff;
    --ink: #111111;
    --gold-deep: #c4903f;
    --gold-mid: #e2bd70;
    --gold-light: #f6eca6;
    --gold-soft: #ead69a;
    --cream: #f2e3b4;
    --rule: #9a9a9a;
    --photo-navy: #22304f;
    --photo-warm: #c9a064;
  }
  * { box-sizing: border-box; margin: 0; padding: 0; }
  html, body { width: 1003px; height: 1200px; overflow: hidden; }
  body { background: var(--page-bg); position: relative; }

  .card {
    position: absolute;
    left: 150px;
    width: 703px;
    height: 401px;
    background: var(--card-white);
    overflow: hidden;
  }
  .card--front { top: 144px; }
  .card--back { top: 654px; }

  .gold-band {
    position: absolute;
    left: 0; right: 0;
  }
  .card--front .gold-band {
    top: 205px; bottom: 0;
    background: linear-gradient(90deg, var(--gold-deep) 0%, var(--gold-mid) 22%, var(--gold-light) 45%, var(--gold-light) 55%, var(--gold-mid) 82%, var(--gold-deep) 100%);
  }
  .card--back .gold-band {
    top: 0; height: 122px;
    background: linear-gradient(90deg, var(--gold-deep) 0%, var(--gold-mid) 25%, var(--gold-soft) 50%, var(--gold-mid) 78%, var(--gold-deep) 100%);
  }
  .gold-band--right {
    position: absolute;
    top: 0; right: 0;
    width: 248px; height: 205px;
    background: linear-gradient(90deg, var(--gold-mid), var(--gold-deep));
  }

  .name-art { position: absolute; left: 0; top: 0; width: 703px; height: 401px; }
  .name-art text {
    font-family: "Playfair Display", serif;
    font-weight: 800;
    font-size: 92px;
    letter-spacing: -1px;
  }

  .title {
    position: absolute;
    font-family: "Raleway", sans-serif;
    font-weight: 300;
    color: var(--ink);
    text-transform: uppercase;
  }
  .card--front .title {
    left: 53px; top: 253px;
    font-size: 30px;
    line-height: 37px;
    letter-spacing: 0.5px;
  }
  .card--back .title {
    left: 39px; top: 203px;
    font-size: 21.5px;
    letter-spacing: 0.3px;
  }

  .dotted-rule {
    position: absolute;
    left: 39px; top: 252px;
    width: 124px;
    border-top: 3px dotted var(--ink);
  }

  .contact-list {
    position: absolute;
    left: 38px; top: 281px;
    width: 417px;
    list-style: none;
    font-family: "Poppins", sans-serif;
    font-size: 16.5px;
    color: var(--ink);
  }
  .contact-list li {
    display: flex;
    align-items: center;
    height: 25.5px;
  }
  .contact-icon { width: 14px; height: 14px; margin-right: 5px; flex: none; }
  .contact-line {
    flex: 1;
    border-top: 1px solid var(--rule);
    margin-left: 12px;
    margin-top: 10px;
  }

  .portrait {
    position: absolute;
    left: 455px; top: 28px;
    width: 248px; height: 373px;
    background: linear-gradient(180deg, var(--photo-warm) 0%, var(--photo-warm) 40%, var(--photo-navy) 62%, var(--photo-navy) 100%);
    border-radius: 110px 110px 0 0;
  }
</style>
</head>
<body>

  <section class="card card--front" aria-label="Card front">
    <div class="gold-band"></div>
    <svg class="name-art" viewBox="0 0 703 401" aria-label="Leonard Vasko">
      <defs>
        <linearGradient id="surname-gold" x1="0" x2="1" y1="0" y2="0">
          <stop offset="0" stop-color="#d2a04c"/>
          <stop offset="1" stop-color="#f7ec9f"/>
        </linearGradient>
      </defs>
      <text x="53" y="135" fill="#111111">LEONARD</text>
      <text x="53" y="205" fill="url(#surname-gold)">VASKO</text>
    </svg>
    <p class="title">Commercial Loan<br>Originator</p>
  </section>

  <section class="card card--back" aria-label="Card back">
    <div class="gold-band"></div>
    <div class="gold-band--right"></div>
    <svg class="name-art" viewBox="0 0 703 401" aria-label="Leonard Vasko">
      <defs>
        <linearGradient id="firstname-cream" x1="0" x2="1" y1="0" y2="0">
          <stop offset="0" stop-color="#ffffff"/>
          <stop offset="0.45" stop-color="#ffffff"/>
          <stop offset="1" stop-color="#f2e3b4"/>
        </linearGradient>
      </defs>
      <text x="40" y="120" fill="url(#firstname-cream)">LEONARD</text>
      <text x="40" y="194" fill="#111111">VASKO</text>
    </svg>
    <p class="title">Commercial Loan Originator</p>
    <div class="dotted-rule"></div>
    <ul class="contact-list">
      <li>
        <svg class="contact-icon" viewBox="0 0 14 14" aria-hidden="true"><circle cx="7" cy="7" r="7" fill="#111"/><rect x="4.5" y="3.5" width="5" height="7" fill="#fff"/><rect x="5.5" y="4.5" width="1" height="1" fill="#111"/><rect x="7.5" y="4.5" width="1" height="1" fill="#111"/><rect x="5.5" y="6.5" width="1" height="1" fill="#111"/><rect x="7.5" y="6.5" width="1" height="1" fill="#111"/></svg>
        (800) 417-2906 x71
      </li>
      <li>
        <svg class="contact-icon" viewBox="0 0 14 14" aria-hidden="true"><circle cx="7" cy="7" r="7" fill="#111"/><path d="M4.3 4.2c.4-.4.9-.4 1.1 0l.6 1c.2.3.1.6-.1.8l-.4.4c.4.9 1.1 1.6 2 2l.4-.4c.2-.2.5-.3.8-.1l1 .6c.4.2.4.7 0 1.1l-.5.5c-.5.4-1.4.3-2.6-.5-1.1-.7-2-1.6-2.7-2.7-.8-1.2-.9-2.1-.5-2.6z" fill="#fff"/></svg>
        (215) 463-0712
      </li>
      <li>
        <svg class="contact-icon" viewBox="0 0 14 14" aria-hidden="true"><circle cx="7" cy="7" r="7" fill="#111"/><rect x="3.8" y="4.8" width="6.4" height="4.4" fill="#fff"/><path d="M3.8 4.8 7 7.4l3.2-2.6" fill="none" stroke="#111" stroke-width="0.8"/></svg>
        l.vasko41@quillbox.example
        <span class="contact-line"></span>
      </li>
    </ul>
    <div class="portrait" role="img" aria-label="Portrait photo of Leonard Vasko in a navy suit"></div>
  </section>

</body>
</html>
```